Classy, Elegant, Simple Business Card Design

Looking to have a classy, simple, and elegant design. Want a top notch designed business card. I really like the look of the new torvane credit card. I also like the design I attached. I am trying to reach 21-29 year old females for booking us for there wedding or event. We offer Disc Jockey Service, Photo Booth Rentals, and Uplighting .

Target Market(s)

21-28 year old females

Contact Information for Business Card

Has to have logo, website, email, and phone number

Font styles to use
Other font styles liked:
• open to font choice, modern, clean
Designer to choose
33a6d7
0791cd
0555a3
ffffff

Requirements
Must have
• Has to have logo, website, email, and phone number
Nice to have
• I really like the design of the new torvane credit card. I also included my logo and some designs I like
Should not have
• clutter or too much info

```html
<!DOCTYPE html>
<html lang="en">
<head>
<meta charset="UTF-8">
<title>Lumenbeat Event Group – Business Card</title>
<link rel="stylesheet" href="https://fonts.googleapis.com/css2?family=Montserrat:wght@300;400;700&family=Roboto:wght@400&display=swap">
<style>
  :root {
    --backdrop: #3a3a3c;
    --card: #1f2023;
    --sky: #33a6d7;
    --azure: #0791cd;
    --deep: #0555a3;
    --white: #ffffff;
    --muted: #9a9ca1;
  }
  * { margin: 0; padding: 0; box-sizing: border-box; }
  html, body { width: 799px; height: 1200px; overflow: hidden; }
  body {
    background: var(--backdrop);
    font-family: "Montserrat", sans-serif;
    position: relative;
  }
  .card {
    position: absolute;
    left: 80px;
    width: 640px;
    height: 366px;
    background: var(--card);
    border-radius: 4px;
    box-shadow: 0 18px 40px rgba(0,0,0,.45);
    overflow: hidden;
  }
  .card--front { top: 150px; }
  .card--back { top: 690px; }

  /* Front */
  .front-mark {
    position: absolute;
    left: 50%; top: 50%;
    transform: translate(-50%, -50%);
    display: flex;
    align-items: center;
    gap: 16px;
  }
  .front-mark__dot {
    width: 22px; height: 22px;
    border-radius: 50%;
    background: var(--azure);
  }
  .front-mark__name {
    font-weight: 300;
    font-size: 44px;
    letter-spacing: 2px;
    color: var(--azure);
  }

  /* Back */
  .brand {
    position: absolute;
    left: 40px; top: 38px;
    font-weight: 300;
    font-size: 30px;
    letter-spacing: 3px;
    text-transform: uppercase;
    color: var(--white);
  }
  .person {
    position: absolute;
    left: 40px; top: 118px;
  }
  .person__name {
    font-weight: 700;
    font-size: 22px;
    color: var(--azure);
  }
  .person__role {
    font-family: "Roboto", sans-serif;
    font-size: 14px;
    color: var(--white);
    margin-top: 2px;
  }
  .contact {
    position: absolute;
    right: 60px; top: 190px;
    list-style: none;
    font-family: "Roboto", sans-serif;
    font-size: 16px;
    color: var(--white);
  }
  .contact__item {
    display: flex;
    align-items: center;
    gap: 12px;
    height: 24px;
  }
  .contact__icon { width: 14px; height: 14px; fill: var(--azure); flex: none; }
  .equalizer-band {
    position: absolute;
    left: 0; right: 0; bottom: 0;
    height: 150px;
    background: linear-gradient(180deg, rgba(51,166,215,0) 0%, rgba(7,145,205,.55) 45%, var(--deep) 100%);
    clip-path: polygon(0 10%, 30% 35%, 60% 55%, 100% 70%, 100% 100%, 0 100%);
  }
</style>
</head>
<body>
  <section class="card card--front" aria-label="Card front">
    <div class="front-mark">
      <span class="front-mark__dot"></span>
      <span class="front-mark__name">Lumenbeat</span>
    </div>
  </section>

  <section class="card card--back" aria-label="Card back">
    <div class="brand">Lumenbeat Event Group</div>
    <div class="person">
      <div class="person__name">Evan Carter</div>
      <div class="person__role">Founder &amp; CEO</div>
    </div>
    <ul class="contact">
      <li class="contact__item">
        <svg class="contact__icon" viewBox="0 0 24 24"><path d="M6.6 10.8a15.1 15.1 0 0 0 6.6 6.6l2.2-2.2a1 1 0 0 1 1-.25 11.4 11.4 0 0 0 3.6.57 1 1 0 0 1 1 1V20a1 1 0 0 1-1 1A17 17 0 0 1 3 4a1 1 0 0 1 1-1h3.5a1 1 0 0 1 1 1c0 1.25.2 2.45.57 3.57a1 1 0 0 1-.25 1z"/></svg>
        614 7720 3381
      </li>
      <li class="contact__item">
        <svg class="contact__icon" viewBox="0 0 24 24"><path d="M2 5h20v14H2z M2 5l10 8 10-8" fill="none" stroke="#0791cd" stroke-width="2"/></svg>
        evan@lumenbeat.com
      </li>
      <li class="contact__item">
        <svg class="contact__icon" viewBox="0 0 24 24"><circle cx="12" cy="12" r="9" fill="none" stroke="#0791cd" stroke-width="2"/><path d="M3 12h18M12 3c3 3 3 15 0 18M12 3c-3 3-3 15 0 18" fill="none" stroke="#0791cd" stroke-width="1.6"/></svg>
        www.lumenbeat.com
      </li>
    </ul>
    <div class="equalizer-band" role="img" aria-label="Blue sound equalizer bars rising along the bottom edge"></div>
  </section>
</body>
</html>
```